Corvin Ridge Software PowerPoint template

We are a software company selling endpoint visibility, access and security technology to enterprise-level IT departments.
Our technology helps organizations gain comprehensive visibility into and control over devices accessing their corporate network so they can quickly identify and address suspicious activity on the network that could lead to potential threats like data breaches.
This technology can cost organizations upwards of $1M - depending on the size of the organization. Our primary clients are Vestral 2,000 companies.
We want a professional, polished PowerPoint template that we can use for all company presentations. Please include:
Title page
Section page
General info page
Thank you page
Logo options and color specs are attached.
Please include our tagline on at least the title page: Discover the edge. Optimize the whole.
Reason: Seeking more options. Looking for a clean design that uses lots of white space.
Software

```html
<!DOCTYPE html>
<html lang="en">
<head>
<meta charset="utf-8">
<title>Corvin Ridge Software – Content Slide</title>
<link href="https://fonts.googleapis.com/css2?family=Roboto+Condensed:wght@700&family=Questrial&family=Didact+Gothic&display=swap" rel="stylesheet">
<style>
  :root {
    --brand-red: #b3161d;
    --brand-orange: #de7f52;
    --ink: #2b2b2b;
    --rule: #d6d6d6;
    --paper: #ffffff;
  }
  * { margin: 0; padding: 0; box-sizing: border-box; }
  html, body { width: 1200px; height: 900px; overflow: hidden; background: var(--paper); }
  .slide { position: relative; width: 1200px; height: 900px; background: var(--paper); }

  .slide-title {
    position: absolute; left: 24px; top: 22px;
    font-family: "Roboto Condensed", "Arial Narrow", sans-serif;
    font-weight: 700; font-size: 46px; letter-spacing: -0.5px; line-height: 1;
    color: var(--brand-red);
  }
  .slide-title .accent { color: var(--brand-orange); }

  .header-rule {
    position: absolute; left: 0; right: 0; top: 80px;
    height: 1px; background: var(--rule);
  }

  .brand {
    position: absolute; right: 22px; top: 18px;
    display: flex; align-items: center; gap: 12px;
  }
  .brand-mark { width: 16px; height: 16px; border-radius: 50%; background: var(--brand-orange); }
  .brand-name {
    font-family: "Questrial", "Century Gothic", sans-serif;
    font-size: 22px; line-height: 1.1; letter-spacing: 3px;
    color: var(--brand-red); text-transform: uppercase; text-align: center;
  }

  .feature {
    position: absolute; left: 0; width: 1200px; height: 290px;
  }
  .feature--first { top: 145px; }
  .feature--second { top: 506px; }

  .feature-image {
    position: absolute; left: 41px; top: 0;
    width: 284px; height: 284px; border-radius: 50%;
    background: var(--brand-orange);
    display: flex; align-items: center; justify-content: center;
    font-family: "Questrial", "Century Gothic", sans-serif;
    font-size: 27px; font-weight: 700; color: #fff;
  }

  .feature-subtitle {
    position: absolute; left: 388px; top: -5px;
    font-family: "Questrial", "Century Gothic", sans-serif;
    font-weight: 700; font-size: 25px; color: var(--brand-orange);
  }
  .feature-body {
    position: absolute; left: 384px; top: 34px; width: 796px;
    font-family: "Didact Gothic", "Century Gothic", sans-serif;
    font-size: 19.5px; line-height: 30px; color: var(--ink);
  }

  .footer {
    position: absolute; left: 0; bottom: 0; width: 1200px; height: 42px;
    background: var(--brand-orange); color: #fff;
    font-family: "Roboto Condensed", "Arial Narrow", sans-serif; font-weight: 700;
    font-size: 17px; display: flex; align-items: center; justify-content: space-between;
    padding: 4px 14px 0 12px;
  }
</style>
</head>
<body>
<main class="slide">
  <h1 class="slide-title">PROJECT <span class="accent">TITLE HERE</span></h1>

  <div class="brand">
    <span class="brand-mark" aria-hidden="true"></span>
    <span class="brand-name">Corvin Ridge<br>Software</span>
  </div>

  <div class="header-rule"></div>

  <section class="feature feature--first">
    <div class="feature-image" role="img" aria-label="Image placeholder">Images</div>
    <h2 class="feature-subtitle">Subtitle Here</h2>
    <p class="feature-body">Odio possim splendide sea cu. Qui nibh mazim insolens ei, tritani suscipit petentium vis ut. His ex reque dissentiet. Mel vocent numquam et, cetero vocent abhorreant cum ut, sit dictas vivendum eu. Ei eos officiis eleifend expetenda, per ei adhuc decore euismod, quando equidem mei an. Novum adipiscing mea ad, Odio possim splendide sea cu. Qui nibh mazim insolens ei, tritani suscipit petentium vis ut. His ex reque dissentiet. Mel vocent numquam et, cetero vocent abhorreant cum ut, sit dictas vivendum eu. Ei eos officiis eleifend expetenda, per ei adhuc decore euismod,</p>
  </section>

  <section class="feature feature--second">
    <div class="feature-image" role="img" aria-label="Image placeholder">Images</div>
    <h2 class="feature-subtitle">Subtitle Here</h2>
    <p class="feature-body">Odio possim splendide sea cu. Qui nibh mazim insolens ei, tritani suscipit petentium vis ut. His ex reque dissentiet. Mel vocent numquam et, cetero vocent abhorreant cum ut, sit dictas vivendum eu. Ei eos officiis eleifend expetenda, per ei adhuc decore euismod, quando equidem mei an. Novum adipiscing mea ad, Odio possim splendide sea cu. Qui nibh mazim insolens ei, tritani suscipit petentium vis ut. His ex reque dissentiet. Mel vocent numquam et, cetero vocent abhorreant cum ut, sit dictas vivendum eu. Ei eos officiis eleifend expetenda, per ei adhuc decore euismod,</p>
  </section>

  <footer class="footer">
    <span class="footer-copyright">COPYRIGHT TEXT HERE</span>
    <span class="footer-page">Page : 01</span>
  </footer>
</main>
</body>
</html>
```